Counseling Practice Business Card

I need a professional looking business card incorporating my new logo that was just completed. Card needs to incorporate my name and title, description of my specialty, my address, my phone number, my fax number, my email and my website URL. I need to be able to choose design on/with different paper colors and textures.
I do not have a lot of business card ideas so I am open to anything but I want bold,sharp, clear card without additional designs other than my logo (see attached file info). I am open to different color backgrounds or paper colors including black. I do not like traditional brackets around area codes in phone number or dashes between numbers in phone number. Am open to other ways of presenting including periods between numbers as appropriate. I do not know enough to know what I like yet but I want card to coordinate and work together with my logo. My practice emphasizes natural mental health interventions so any use of color (with background paper color or the blue and green in my logo) that elicits nature is nice. In addition to black, any natural brown or wood looking background might be desirable also. Most of the offerings so far look very similar and boring.

Target Market(s)

Potential therapy clients and other professionals

Contact Information for Business Card

Card information:
Gerald M. Whitcombe, Ph.D.
Licensed Clinical Psychologist
Integrative Health Coach
4812 Marlowe Ridge Blvd SE
Suite 310
Alder Glen, GA 30412
(770) 415-2983 phone
(770) 581-4096 fax
drgeraldwhitcombe@quillmarsh.net
brightfernwellness.net

Font styles to use
Serif
Sans Serif
Other font styles liked:
• anything that you think looks crisp, clear and easily readable

Requirements
Must have
• Any color used should coordinate with my logo design (see attached files).
• Card should be printed horizontally so top and bottom are longest sides of rectangle.
• Background color or paper color should complement and highlight logo. Do not like a white background. black, grey, brown or any color my logo would blend well with.
Nice to have
• I would like designer to utilize color to highlight letters/name or phone-fax-web symbols.
• Bottom edge of card could be highlighted if appropriate to an idea.
Should not have
• I would NOT want the card to have a pure white background at all.
• No clear cards.
• Cards should be oriented with long sides on bottom and top, NOT sides. DO NOT LIKE THIS THIN TALL ORIENTATION.

```html
<!DOCTYPE html>
<html lang="en">
<head>
<meta charset="utf-8">
<title>Brightfern Wellness Business Card</title>
<link href="https://fonts.googleapis.com/css2?family=Open+Sans:wght@400;600&display=swap" rel="stylesheet">
<style>
  :root {
    --backdrop: #2a2a2c;
    --card-top: #141414;
    --card-bottom: #060606;
    --brand-blue: #2e7cc6;
    --brand-green: #1f8a4c;
    --text-light: #e6e6e6;
    --rule: #3a3a3a;
  }
  * { margin: 0; padding: 0; box-sizing: border-box; }
  html, body {
    width: 1200px; height: 900px; overflow: hidden;
    background: var(--backdrop);
    font-family: "Open Sans", Arial, sans-serif;
  }
  .canvas {
    width: 1200px; height: 900px;
    display: flex; flex-direction: column; align-items: center; justify-content: center;
    gap: 50px;
  }
  .card {
    position: relative;
    width: 560px; height: 320px;
    background: linear-gradient(160deg, var(--card-top), var(--card-bottom));
    overflow: hidden;
  }
  .card__edge {
    position: absolute; left: 0; right: 0; bottom: 0;
    height: 10px; background: var(--brand-blue);
  }
  .card--front {
    display: flex; align-items: center; justify-content: center;
  }
  .brand-name {
    font-weight: 600; font-size: 42px; color: var(--brand-blue);
    letter-spacing: 0.5px; margin-bottom: 10px;
  }
  .card--back {
    display: flex; flex-direction: column; align-items: center;
    padding-top: 28px; text-align: center; color: var(--text-light);
    font-size: 16px; line-height: 1.35;
  }
  .person-name { font-weight: 600; font-size: 16px; letter-spacing: 0.5px; text-transform: uppercase; }
  .person-name .first { color: var(--brand-blue); }
  .person-name .last { color: var(--brand-green); }
  .divider { width: 220px; height: 1px; background: var(--rule); margin: 8px 0; }
  .label { color: var(--brand-blue); }
  .web { color: var(--brand-blue); }
  .web .domain { color: var(--brand-green); }
</style>
</head>
<body>
<main class="canvas">
  <section class="card card--front">
    <p class="brand-name">Brightfern Wellness</p>
    <div class="card__edge"></div>
  </section>

  <section class="card card--back">
    <p class="person-name"><span class="first">Gerald M.</span> <span class="last">Whitcombe,</span> <span class="first">Ph.D.</span></p>
    <p>Licensed Clinical Psychologist /</p>
    <p>Integrative Health Coach</p>
    <div class="divider"></div>
    <p><span class="label">P:</span> 770. 415.2983</p>
    <p><span class="label">F:</span> 770. 581.4096</p>
    <p><span class="label">E:</span> drgeraldwhitcombe@quillmarsh.net</p>
    <p class="web">www.<span class="domain">brightfernwellness</span>.net</p>
    <div class="divider"></div>
    <p>4812 Marlowe Ridge Blvd SE</p>
    <p>Suite 310 Alder Glen, GA 30412</p>
    <div class="card__edge"></div>
  </section>
</main>
</body>
</html>
```